The most modern business card ever !!!

Our company call “Vendalo”. Vendalo is a technology company specialized in cruises solutions. Out main product is a platform to reserve cruises. This is a revolutionary platform that make easier to travel agencies and final users to reserve cruises across dozen companies like tibba, wernu, hpv, dgb, etc..We are a “start up”, with a young team of developers and we want to transmit it.. For it, we want something different, a modern business card that represent cruises and technology.. When someone receive this card, this person should say: wowww this is different… this is modern… this is a cruise related company..
- diferent, modern
- traditions business card

```html
<!DOCTYPE html>
<html lang="en">
<head>
<meta charset="utf-8">
<title>Vendalo Business Card</title>
<link rel="stylesheet" href="https://fonts.googleapis.com/css2?family=Open+Sans:wght@400;600&family=Roboto+Condensed:wght@400;700&display=swap">
<style>
  :root{
    --canvas:#eceff2;
    --ink-dark:#2b2a2c;
    --tab-dark:#3b3a3d;
    --sea-light:#2fa9de;
    --sea-mid:#2395c7;
    --sea-deep:#17729c;
    --shoulder:#26343d;
    --sky-top:#3a63c9;
    --sky-bottom:#58c4ec;
    --white:#ffffff;
    --navy:#14385e;
    --icon-bg:#151b20;
  }
  *{box-sizing:border-box;margin:0;padding:0}
  html,body{width:1200px;height:1200px;overflow:hidden;background:var(--canvas)}
  .canvas{position:relative;width:1200px;height:1200px}
  .card{position:absolute;top:215px;width:440px;height:770px;border-radius:6px;overflow:hidden;box-shadow:0 12px 30px rgba(0,0,0,.18)}
  .card--back{left:120px;background:var(--ink-dark)}
  .card--front{left:640px;background:linear-gradient(180deg,var(--sea-mid),var(--sea-deep))}
  .photo{position:absolute;left:0;top:0;width:440px;height:300px}
  .card--back .photo{background:linear-gradient(170deg,var(--sky-top) 0%,#4f9fe4 45%,var(--sky-bottom) 100%)}
  .card--front .photo{background:linear-gradient(180deg,#6f8fd6 0%,#a9c7e8 55%,#3f7fb4 100%)}
  .card-shapes{position:absolute;left:0;top:0;width:440px;height:770px}
  .web-address{position:absolute;left:0;top:262px;width:440px;text-align:center;font-family:"Roboto Condensed",sans-serif;font-size:30px;color:var(--white);letter-spacing:1px}
  .tagline{position:absolute;left:0;top:390px;width:440px;text-align:center;font-family:"Open Sans",sans-serif;font-size:27px;line-height:1.65;color:var(--white)}
  .brand{position:absolute;left:28px;top:28px;font-family:"Roboto Condensed",sans-serif;font-weight:700;font-size:46px;color:var(--navy);letter-spacing:1px}
  .holder{position:absolute;left:0;top:272px;width:440px;text-align:center;color:var(--white);font-family:"Roboto Condensed",sans-serif}
  .holder-name{font-size:38px;letter-spacing:1px;line-height:1.1}
  .holder-role{font-size:19px;letter-spacing:1px}
  .contacts{position:absolute;left:0;top:380px;width:440px;list-style:none;text-align:center;color:var(--white);font-family:"Roboto Condensed",sans-serif;font-size:21px}
  .contact{display:flex;flex-direction:column;align-items:center;margin-bottom:16px}
  .contact svg{width:26px;height:26px;margin-bottom:6px}
</style>
</head>
<body>
<main class="canvas">

  <section class="card card--back">
    <div class="photo" role="img" aria-label="Photo of a white cruise ship sailing on blue sea under a bright sky"></div>
    <svg class="card-shapes" viewBox="0 0 440 770" aria-hidden="true">
      <path d="M0 300 L0 245 L40 245 L60 300 Z" fill="var(--ink-dark)"/>
      <path d="M440 300 L440 245 L400 245 L380 300 Z" fill="var(--ink-dark)"/>
      <path d="M45 248 L395 248 L362 322 Q356 334 342 334 L98 334 Q84 334 78 322 Z" fill="var(--tab-dark)"/>
    </svg>
    <p class="web-address">www.vendalo.com</p>
    <p class="tagline">Vendalo is a<br>technology company<br>specialized in<br>cruises solutions</p>
  </section>

  <section class="card card--front">
    <div class="photo" role="img" aria-label="Photo of a large cruise ship with a painted hull on open water"></div>
    <p class="brand">Vendalo</p>
    <svg class="card-shapes" viewBox="0 0 440 770" aria-hidden="true">
      <path d="M0 300 L0 250 L40 250 L62 300 Z" fill="var(--shoulder)"/>
      <path d="M440 300 L440 250 L400 250 L378 300 Z" fill="var(--shoulder)"/>
      <path d="M45 252 L395 252 L362 332 Q356 345 340 345 L100 345 Q84 345 78 332 Z" fill="var(--sea-light)"/>
    </svg>
    <div class="holder">
      <p class="holder-name">Marco Reyes</p>
      <p class="holder-role">Director</p>
    </div>
    <ul class="contacts">
      <li class="contact">
        <svg viewBox="0 0 26 26" aria-hidden="true"><circle cx="13" cy="13" r="13" fill="var(--icon-bg)"/><rect x="7" y="9" width="12" height="8" fill="none" stroke="#fff" stroke-width="1.5"/><path d="M7 9 L13 14 L19 9" fill="none" stroke="#fff" stroke-width="1.5"/></svg>
        <span>marco@vendalo.com</span>
      </li>
      <li class="contact">
        <svg viewBox="0 0 26 26" aria-hidden="true"><circle cx="13" cy="13" r="13" fill="var(--icon-bg)"/><path d="M7 11 Q13 6 19 11 L17 13 L15 11 L11 11 L9 13 Z" fill="#fff"/><rect x="9" y="13" width="8" height="5" rx="1" fill="#fff"/></svg>
        <span>1-555-014290</span>
      </li>
      <li class="contact">
        <svg viewBox="0 0 26 26" aria-hidden="true"><circle cx="13" cy="13" r="13" fill="var(--icon-bg)"/><circle cx="13" cy="13" r="6" fill="none" stroke="#fff" stroke-width="1.5"/><ellipse cx="13" cy="13" rx="2.5" ry="6" fill="none" stroke="#fff" stroke-width="1.2"/><line x1="7" y1="13" x2="19" y2="13" stroke="#fff" stroke-width="1.2"/></svg>
        <span>www.vendalo.com</span>
      </li>
      <li class="contact">
        <svg viewBox="0 0 26 26" aria-hidden="true"><circle cx="13" cy="13" r="13" fill="var(--icon-bg)"/><path d="M13 20 Q8 14 8 11 A5 5 0 0 1 18 11 Q18 14 13 20 Z" fill="#fff"/><circle cx="13" cy="11" r="2" fill="var(--icon-bg)"/></svg>
        <span>Harbor City, Seaview Land</span>
      </li>
    </ul>
  </section>

</main>
</body>
</html>
```